Give Gold Kite an Online Presence!

Gold Kite Property Maintenance is an Australian Owned property maintenance company who needs a stand out online presence.

GK maintains many buildings and sites and wants to appeal to a corporate professional market with their brand new website. GK is essentially a handyman service offering all maintenance services to home owners, office managers, real estate agents and strata managers.

The Website:
We need a corporate website that appeals to our broader customer base (property owners, property managers, office managers) the copy is being written by a professional so use filler text for now.

Things that we want:
Home page that sets us apart and appeals to the corporate and residential market. The home page needs to not focus on either the residential or commercial market. The home page should focus on our logo and branding. We have a logo already and it is attached to the brief, please use it and try to consider the colour pallette that goes with it. Whilst we want the site to appear strong and manly it is important to remember that 95% of our customers are female so we need the site to be appealing to women. Women need to believe that we are strong, dependable and trustworthy.
We'd like a quote page and potentially also the ability to get a quote from the home page (please don't put it in if it ruins the overall feel of the home page)
An "about us" page
A contact us page
A blog that's built in (we don't want to link to an external blog)
(overall we'd expect to have 6 or 7 pages total)

The site will also need coding - we expect this to be done in a separate project but need you to consider a few things about the coding side of things.

It needs to be iPhone and iPad compatible.

We'd like you to suggest the best CMS that you would use or if you would suggest not using a CMS please let us know with your submissions.

Target Market(s)

Property owners, office managers and property managers who need maintenance on buildings (So all of them)

Industry/Entity Type

Property Maintenance

Requirements
Must have
• Our Logo
Home page
About Us
Residential
Commercial
Real Estate/Strata
Contact Us/Quote
Blog
Nice to have
• Quote form included in home page
Movement on the home page at least
Should not have
• other logos, too much colour
NO FLASH

```html
<!DOCTYPE html>
<html lang="en">
<head>
<meta charset="utf-8">
<title>Gold Kite Property Maintenance</title>
<link rel="stylesheet" href="https://fonts.googleapis.com/css2?family=Open+Sans:ital,wght@0,400;0,600;0,700;1,400;1,600;1,700&display=swap">
<style>
  :root {
    --orange: #f58a07;
    --orange-light: #fbb512;
    --red: #d01f1f;
    --ink: #222222;
    --nav: #1c1c1c;
    --text: #555555;
    --muted: #777777;
    --line: #e3e3e3;
    --panel: #f2f2f2;
    --footer: #262626;
    --footer-deep: #141414;
    --green: #2fa31c;
    --white: #ffffff;
  }
  * { box-sizing: border-box; margin: 0; padding: 0; }
  html, body { width: 961px; height: 1200px; overflow: hidden; }
  body { position: relative; background: var(--white); font-family: "Open Sans", Arial, sans-serif; color: var(--text); }
  .abs { position: absolute; }

  /* Header */
  .top-rule { left: 0; top: 0; width: 961px; height: 3px; background: var(--red); }
  .header { left: 0; top: 3px; width: 961px; height: 101px; background: linear-gradient(#fafafa, #f0f0f0); }
  .brand { left: 88px; top: 27px; display: flex; align-items: center; gap: 10px; }
  .brand-mark { width: 34px; height: 34px; background: var(--orange); }
  .brand-name { font-size: 26px; font-weight: 700; color: var(--ink); line-height: 1; white-space: nowrap; }
  .social { display: flex; gap: 6px; }
  .social span { width: 27px; height: 27px; border-radius: 50%; background: #8a8a8a; display: block; }
  .header .social { right: 86px; top: 14px; }
  .call { right: 86px; top: 50px; font-size: 19px; color: var(--ink); white-space: nowrap; }
  .call b { font-weight: 400; font-size: 15px; }
  .email { right: 86px; top: 74px; font-size: 13px; color: var(--ink); white-space: nowrap; }

  /* Navigation */
  .nav { left: 0; top: 104px; width: 961px; height: 31px; background: var(--nav); }
  .nav ul { list-style: none; position: absolute; left: 0; top: 0; width: 961px; height: 31px; }
  .nav li { position: absolute; top: 0; color: var(--white); font-size: 15px; line-height: 31px; white-space: nowrap; }
  .nav li.active { background: var(--orange); width: 73px; text-align: center; }

  /* Hero */
  .hero { left: 0; top: 135px; width: 961px; height: 405px;
    background: linear-gradient(180deg, #9bb4cc 0%, #c9c3b6 35%, #a38b74 60%, #7b8f55 85%, #8aa858 100%); }
  .hero-figure { left: 597px; top: 135px; width: 195px; height: 405px;
    background: linear-gradient(180deg, #e0b829 0%, #3f5a8e 30%, #34497a 55%, #b48a55 75%, #4a4a4a 100%); opacity: .85; }
  .hero-box { left: 88px; top: 216px; width: 375px; height: 243px; background: rgba(20,20,20,.82); border-radius: 3px; }
  .hero-kicker { left: 22px; top: 11px; font-size: 11px; color: #ddd; white-space: nowrap; }
  .hero-title { left: 20px; top: 22px; font-size: 35px; font-weight: 600; color: var(--orange); letter-spacing: -.5px; white-space: nowrap; }
  .hero-title small { font-size: 11px; font-weight: 400; color: var(--orange-light); letter-spacing: 0; }
  .services { left: 22px; top: 78px; width: 340px; display: grid; grid-template-columns: 189px 150px; row-gap: 5px; list-style: none; }
  .services li { display: flex; align-items: center; gap: 8px; color: var(--white); font-size: 13.5px; font-weight: 600; line-height: 17px; white-space: nowrap; }
  .cta { left: 22px; top: 185px; width: 154px; height: 39px; border-radius: 3px; background: linear-gradient(#fcc21a, #f39a0c); color: var(--white); font-size: 21px; font-weight: 600; text-align: center; line-height: 39px; white-space: nowrap; }
  .contact-name { left: 193px; top: 189px; font-size: 23px; color: var(--white); white-space: nowrap; }

  /* Audience cards */
  .card { top: 574px; width: 242px; height: 213px; border: 1px solid var(--line); background: var(--white); text-align: center; }
  .card .icon { width: 62px; height: 62px; margin: 29px auto 0; border-radius: 50%; border: 4px solid #e8e8e8; display: flex; align-items: center; justify-content: center; }
  .card h3 { margin-top: 29px; font-size: 14px; font-weight: 400; color: #333; letter-spacing: .3px; white-space: nowrap; }
  .card p { margin: 14px auto 0; width: 218px; font-family: Arial, sans-serif; font-size: 10px; line-height: 13px; color: #666; }

  /* Section heads */
  .section-head { display: flex; align-items: center; gap: 6px; height: 16px; }
  .section-head .bar { height: 6px; background: #dcdcdc; }
  .section-head h4 { font-size: 15px; font-weight: 400; color: var(--orange); white-space: nowrap; }
  .arrows { display: flex; gap: 4px; }
  .arrows span { width: 14px; height: 14px; border-radius: 50%; border: 1px solid #bbb; background: #fafafa; display: flex; align-items: center; justify-content: center; }

  .gallery { left: 88px; top: 840px; width: 512px; height: 142px; background: linear-gradient(#ffffff, #ececec); border-radius: 3px; box-shadow: 0 2px 4px rgba(0,0,0,.15); }
  .thumb { top: 20px; width: 104px; height: 103px; }
  .thumb-label { position: absolute; bottom: 8px; width: 100%; text-align: center; color: var(--white); font-size: 13px; }

  .quote-card { left: 632px; top: 868px; width: 241px; height: 114px; background: var(--white); border: 1px solid #ddd; }
  .quote-card p { padding: 8px 7px 0; font-family: Arial, sans-serif; font-style: italic; font-size: 8.8px; line-height: 12.5px; color: #555; }
  .quote-card .byline { position: absolute; left: 0; bottom: 0; width: 100%; height: 22px; background: #dedede; text-align: right; padding-right: 8px; font-family: Arial, sans-serif; font-style: italic; font-size: 10px; line-height: 22px; color: #555; }
  .quote-card .byline b { color: #3a8fd6; font-weight: 400; }
  .avatar { left: 641px; top: 843px; width: 42px; height: 42px; border-radius: 50%; background: linear-gradient(#d8a36c, #b06a3a); border: 3px solid var(--white); box-shadow: 0 0 0 1px #ccc; }

  /* Footer */
  .footer { left: 0; top: 1039px; width: 961px; height: 142px; background: var(--footer); border-top: 2px solid var(--red); }
  .foot-title { font-size: 16px; color: var(--red); white-space: nowrap; }
  .sitemap { list-style: none; display: grid; grid-template-columns: 110px 110px; row-gap: 5px; }
  .sitemap li { font-family: Arial, sans-serif; font-size: 10.5px; color: #aaa; line-height: 14px; white-space: nowrap; }
  .sitemap li::before { content: "\25B8"; margin-right: 5px; font-size: 9px; }
  .sitemap li.current { color: var(--white); }
  .connect { font-size: 20px; font-weight: 700; font-style: italic; color: var(--white); white-space: nowrap; }
  .footer .social span { background: #666; }
  .news-input { left: 647px; top: 1101px; width: 226px; height: 22px; background: var(--white); font-family: Arial, sans-serif; font-style: italic; font-size: 10px; color: #888; padding: 5px 10px; }
  .news-btn { left: 648px; top: 1133px; width: 100px; height: 22px; background: linear-gradient(#45b82a, #239013); color: var(--white); font-family: Arial, sans-serif; font-size: 11px; text-align: center; line-height: 22px; white-space: nowrap; }
  .news-note { left: 756px; top: 1133px; width: 118px; font-family: Arial, sans-serif; font-size: 8.5px; line-height: 11.5px; color: #aaa; }
  .copyright { left: 0; top: 1181px; width: 961px; height: 19px; background: var(--footer-deep); text-align: center; font-family: Arial, sans-serif; font-size: 8px; line-height: 19px; color: #666; }
</style>
</head>
<body>
  <div class="abs top-rule"></div>
  <header class="abs header">
    <div class="abs brand">
      <span class="brand-mark"></span>
      <span class="brand-name">Gold Kite</span>
    </div>
    <div class="abs social" aria-label="Social links">
      <span></span><span></span><span></span><span></span><span></span>
    </div>
    <div class="abs call">Call Us Free: <b>0400 555 210</b></div>
    <div class="abs email">Email: hello@goldkite.example</div>
  </header>

  <nav class="abs nav">
    <ul>
      <li class="active" style="left:88px">Home</li>
      <li style="left:178px">About Us</li>
      <li style="left:275px">Residential</li>
      <li style="left:383px">Commercial</li>
      <li style="left:496px">Real Estate/Strata</li>
      <li style="left:649px">Quote</li>
      <li style="left:726px">Blog</li>
      <li style="left:789px">Contact Us</li>
    </ul>
  </nav>

  <section class="abs hero" role="img" aria-label="Photo of a suburban street with brick homes under a cloudy sky"></section>
  <div class="abs hero-figure" role="img" aria-label="Photo of a tradesman in a hard hat holding a spirit level"></div>
  <div class="abs hero-box">
    <div class="abs hero-kicker">Just some of what the</div>
    <div class="abs hero-title">Gold Kite <small>can do for you</small></div>
    <ul class="abs services">
      <li><svg width="13" height="13" viewBox="0 0 13 13"><circle cx="6.5" cy="6.5" r="6.5" fill="#3cb529"/><path d="M3.5 6.8l2 2 4-4.2" stroke="#fff" stroke-width="1.8" fill="none"/></svg>Carpentry</li>
      <li><svg width="13" height="13" viewBox="0 0 13 13"><circle cx="6.5" cy="6.5" r="6.5" fill="#3cb529"/><path d="M3.5 6.8l2 2 4-4.2" stroke="#fff" stroke-width="1.8" fill="none"/></svg>Office moves</li>
      <li><svg width="13" height="13" viewBox="0 0 13 13"><circle cx="6.5" cy="6.5" r="6.5" fill="#3cb529"/><path d="M3.5 6.8l2 2 4-4.2" stroke="#fff" stroke-width="1.8" fill="none"/></svg>Doors and locks</li>
      <li><svg width="13" height="13" viewBox="0 0 13 13"><circle cx="6.5" cy="6.5" r="6.5" fill="#3cb529"/><path d="M3.5 6.8l2 2 4-4.2" stroke="#fff" stroke-width="1.8" fill="none"/></svg>Painting</li>
      <li><svg width="13" height="13" viewBox="0 0 13 13"><circle cx="6.5" cy="6.5" r="6.5" fill="#3cb529"/><path d="M3.5 6.8l2 2 4-4.2" stroke="#fff" stroke-width="1.8" fill="none"/></svg>Windows and screens</li>
      <li><svg width="13" height="13" viewBox="0 0 13 13"><circle cx="6.5" cy="6.5" r="6.5" fill="#3cb529"/><path d="M3.5 6.8l2 2 4-4.2" stroke="#fff" stroke-width="1.8" fill="none"/></svg>All repairs</li>
      <li><svg width="13" height="13" viewBox="0 0 13 13"><circle cx="6.5" cy="6.5" r="6.5" fill="#3cb529"/><path d="M3.5 6.8l2 2 4-4.2" stroke="#fff" stroke-width="1.8" fill="none"/></svg>Furniture assembly</li>
      <li><svg width="13" height="13" viewBox="0 0 13 13"><circle cx="6.5" cy="6.5" r="6.5" fill="#3cb529"/><path d="M3.5 6.8l2 2 4-4.2" stroke="#fff" stroke-width="1.8" fill="none"/></svg>Lighting</li>
    </ul>
    <div class="abs cta">Contact Us</div>
    <div class="abs contact-name">Daniel Ward</div>
  </div>

  <article class="abs card" style="left:88px">
    <div class="icon"><svg width="20" height="18" viewBox="0 0 20 18" fill="#444"><path d="M10 0L0 6h20z"/><rect x="2" y="7" width="3" height="8"/><rect x="8.5" y="7" width="3" height="8"/><rect x="15" y="7" width="3" height="8"/><rect x="0" y="15.5" width="20" height="2.5"/></svg></div>
    <h3>HOME OWNERS</h3>
    <p>There are many variations of passages or lorem ipsum available, but the majority have been alteration in some form by humor.</p>
  </article>
  <article class="abs card" style="left:360px">
    <div class="icon"><svg width="10" height="20" viewBox="0 0 10 20" fill="#444"><path d="M2.5 0h5l-1 3h-3z"/><path d="M3.5 4h3l2.5 11L5 20 1 15z"/></svg></div>
    <h3>OFFICE MANAGERS</h3>
    <p>There are many variations of passages or lorem ipsum available, but the majority have been alteration in some form by humor.</p>
  </article>
  <article class="abs card" style="left:632px">
    <div class="icon"><svg width="22" height="16" viewBox="0 0 22 16" fill="#444"><circle cx="8" cy="4" r="4"/><path d="M0 16c0-5 3.5-7 8-7s8 2 8 7z"/><circle cx="15.5" cy="4.5" r="3.2"/><path d="M14 9c5 0 8 2 8 6h-4.5c0-2.5-1.2-4.5-3.5-6z"/></svg></div>
    <h3>REAL ESTATE AGENTS</h3>
    <p>There are many variations of passages or lorem ipsum available, but the majority have been alteration in some form by humor.</p>
  </article>

  <div class="abs section-head" style="left:88px; top:816px; width:512px">
    <span class="bar" style="width:14px"></span>
    <h4>Work Gallery</h4>
    <span class="bar" style="flex:1"></span>
    <span class="arrows"><span><svg width="6" height="6" viewBox="0 0 6 6"><path d="M4 0L1 3l3 3" stroke="#999" fill="none"/></svg></span><span><svg width="6" height="6" viewBox="0 0 6 6"><path d="M2 0l3 3-3 3" stroke="#999" fill="none"/></svg></span></span>
    <span class="bar" style="width:12px"></span>
  </div>
  <section class="abs gallery">
    <div class="abs thumb" style="left:15px; background:linear-gradient(#bcd3e6 0%, #c9c2b4 45%, #8a7a63 65%, #5f8a3a 100%)" role="img" aria-label="Photo of a renovated house front with garden"></div>
    <div class="abs thumb" style="left:141px; background:linear-gradient(#4a4a4a, #2e2e2e 70%, #565656)" role="img" aria-label="Photo of a dark interior stairwell"><span class="thumb-label">Interior</span></div>
    <div class="abs thumb" style="left:268px; background:linear-gradient(#d9d6d0, #f3f2ee 55%, #9a8f80)" role="img" aria-label="Photo of a white modern kitchen"></div>
    <div class="abs thumb" style="left:394px; background:linear-gradient(90deg, #6d6d6d, #e8e8e8 45%, #f7f7f7)" role="img" aria-label="Photo of a bathroom with white fixtures"></div>
  </section>

  <div class="abs section-head" style="left:632px; top:816px; width:241px">
    <span class="bar" style="width:12px"></span>
    <h4>Testimonial</h4>
    <span class="bar" style="flex:1"></span>
    <span class="arrows"><span><svg width="6" height="6" viewBox="0 0 6 6"><path d="M4 0L1 3l3 3" stroke="#999" fill="none"/></svg></span><span><svg width="6" height="6" viewBox="0 0 6 6"><path d="M2 0l3 3-3 3" stroke="#999" fill="none"/></svg></span></span>
    <span class="bar" style="width:10px"></span>
  </div>
  <blockquote class="abs quote-card">
    <p style="padding-top:22px">There are many variations of passages of Lorem Ipsum available, but the majority have suffered alteration in some form, by injected humour,</p>
    <p style="padding-top:5px">Lorem Ipsum is simply dummy text of the printing and</p>
    <div class="byline"><b>Helen Price</b>, Sydney</div>
  </blockquote>
  <div class="abs avatar" role="img" aria-label="Customer portrait"></div>

  <footer class="abs footer">
    <div class="abs foot-title" style="left:90px; top:33px">Site Map</div>
    <ul class="abs sitemap" style="left:90px; top:60px">
      <li class="current">Home</li><li>Real Estate/Strata</li>
      <li>About Us</li><li>Quote</li>
      <li>Residential</li><li>Blog</li>
      <li>Commercial</li><li>Contact Us</li>
    </ul>
    <div class="abs connect" style="left:377px; top:54px">Connect With Us</div>
    <div class="abs social" style="left:380px; top:93px" aria-label="Social links">
      <span></span><span></span><span></span><span></span><span></span>
    </div>
    <div class="abs foot-title" style="left:647px; top:33px">Subscribe Newsletter</div>
  </footer>
  <div class="abs news-input">Email Address</div>
  <div class="abs news-btn">Subscribe Now</div>
  <div class="abs news-note">Free Subscribe our latest offers and Plans.</div>
  <div class="abs copyright">Copy &copy; 2012 Gold Kite Property Maintenance. All rights reserved.</div>
</body>
</html>
```